Kelvo bottle Label (Yoghurt drink)

Label for a 300 ml yoghurt drink bottle in 3 flavours.

General description:
• This is to design a sleeve shrink label for a Yoghurt Drink bottle in three flavours, Classic, Strawberry and Blueberry.
• Attached 3 photos: The one with KELVO brand in the current design we want to replace using the same bottle.
• Graphically, the design is to be similar to the examples provided for drumelo and fizzcrate.
• Use font and barcode size to be readable and legal.
• Minimize the use of the upper third of the bottle as it will be distorted when the label shrinks to the bottle.
• Professional and experienced designers only are welcome, please do not waste your time otherwise.

Bottle dimensions:
• Base across: 61 mm
• Height: 145 mm (approximate)

Graphical description:
• White colour with bands at the top and bottom similar to the one in “drumelo” example provided (not necessarily identical, feel free to be creative.
• The upper and lower bands to be: Green for “classic”, Pink or red for strawberry and purple for blueberry flavour.
• On the front: the brand name “Kelvo” and description “Yoghurt Drink” to be graphically attractive.
• On the front: two or more pieces of strawberry or blueberry for each flavour placed nicely with the option to include “yoghurt splash” or any suitable affects you deem suitable.
• For the Classic flavour, use the words (Classic, Lassi, Ayran) in the same location for the berries done in a graphically suitable manner.
• Colour temperature for the three flavours to be similar.

Information and objects on the label:
Front:
• The word “Kelvo” (brand name)
• “Yoghurt drink” (Product description)
• “300 ml” (size)
• Picture of Strawberries for strawberry flavour.
• Picture of Blueberries for blueberry flavour.
• The words (Classic, Lassi, Ayran) in the place used for the strawberries in the flavoured type, distributed to look graphically suitable for the overall design.

Back:
• Ingredient: Milk/milk solids, culture, salt, water, sugar, colour, flavour. (this is to be finalized later)
• Nutrition information table: (to be provided later).
• Barcode (to be provided later)
• Product of Australia
• Morel Tunsley Pty Ltd, 5/14 Ferrit St, Malaga, WA 6090
• info@kelvo-example.com.au 0491 000 372
• Keep under 5⁰ C
• Best before date printed on the bottle
• Shake well (to be located on the side at the top)
• Recycle icon.

Health benefits: (to be located suitably, possibly on the side with vertical orientation)
• Rich in probiotic bacteria and vitamins.
• Improves digestion and bowel motion.
• Supports weight control and fat loss.

Target Market(s)

General consumers

Industry/Entity Type

Grocery Store

Font styles to use
Sans Serif

Colors
abd037
b768aa
f04a50

Requirements
Must have
• The details in the project description
• The design must be simple and neat.
• Please use the shape of the current bottle "Kelvo" as in the attached photo.
Should not have
• Busy, cluttered, or empty and incomplete designs.

```html
<!DOCTYPE html>
<html lang="en">
<head>
<meta charset="utf-8">
<title>Kelvo Yoghurt Drink – Strawberry Label</title>
<link rel="stylesheet" href="https://fonts.googleapis.com/css2?family=Playfair+Display:ital,wght@1,700;1,900&family=Raleway:wght@400;600&display=swap">
<style>
  :root {
    --berry: #e0137f;
    --berry-deep: #c40f6e;
    --label-white: #ffffff;
    --ink: #2b2b2b;
    --bg-top: #f5f5f5;
    --bg-bottom: #b4d3ec;
    --splash-light: #f6cfe0;
    --splash-mid: #ec9fc2;
    --fruit-red: #d8352f;
  }
  * { margin: 0; padding: 0; box-sizing: border-box; }
  html, body { width: 1081px; height: 1200px; overflow: hidden; }
  body {
    background: linear-gradient(180deg, var(--bg-top) 0%, var(--bg-bottom) 100%);
    font-family: "Raleway", sans-serif;
    position: relative;
  }
  .label {
    position: absolute;
    left: 300px; top: 150px;
    width: 480px; height: 930px;
    background: var(--label-white);
    overflow: hidden;
    box-shadow: 0 10px 30px rgba(40, 70, 110, 0.18);
  }
  .band { position: absolute; left: 0; width: 100%; display: block; }
  .band--top { top: 0; height: 170px; }
  .band--bottom { bottom: 0; height: 130px; }

  .brand {
    position: absolute;
    right: 24px; top: 210px;
    width: 180px;
    text-align: center;
  }
  .brand__mark {
    display: inline-block;
    width: 14px; height: 14px;
    background: var(--berry);
    margin-right: 8px;
    vertical-align: middle;
  }
  .brand__name {
    font-family: "Raleway", sans-serif;
    font-weight: 600;
    font-size: 30px;
    letter-spacing: 2px;
    color: var(--berry);
    vertical-align: middle;
  }
  .brand__tagline {
    margin-top: 6px;
    background: var(--berry);
    color: var(--label-white);
    font-size: 11px;
    font-weight: 600;
    letter-spacing: 0.5px;
    line-height: 1.35;
    padding: 4px 8px;
  }

  .product-title {
    position: absolute;
    left: 10px; top: 770px;
    transform: rotate(-90deg);
    transform-origin: 0 0;
    white-space: nowrap;
  }
  .product-title__word {
    font-family: "Playfair Display", serif;
    font-style: italic;
    font-weight: 900;
    font-size: 110px;
    color: var(--berry);
    line-height: 1;
    display: inline-block;
    vertical-align: top;
  }
  .product-title__type {
    display: block;
    font-family: "Raleway", sans-serif;
    font-size: 28px;
    letter-spacing: 14px;
    color: var(--ink);
    margin-left: 220px;
    margin-top: -10px;
  }

  .fruit-visual {
    position: absolute;
    right: 0; top: 380px;
    width: 300px; height: 320px;
    background:
      radial-gradient(circle at 55% 35%, var(--fruit-red) 0 22%, transparent 23%),
      radial-gradient(circle at 80% 18%, var(--fruit-red) 0 14%, transparent 15%),
      radial-gradient(ellipse at 55% 55%, var(--splash-mid) 0 40%, var(--splash-light) 60%, transparent 72%);
    border-radius: 40% 0 0 50%;
  }

  .flavour {
    position: absolute;
    right: 50px; top: 722px;
    font-family: "Playfair Display", serif;
    font-style: italic;
    font-weight: 700;
    font-size: 40px;
    line-height: 1.2;
    color: var(--berry);
  }

  .volume {
    position: absolute;
    right: 18px; bottom: 22px;
    font-family: "Raleway", sans-serif;
    font-size: 34px;
    color: var(--label-white);
  }
</style>
</head>
<body>
  <main class="label">
    <svg class="band band--top" viewBox="0 0 480 170" preserveAspectRatio="none" aria-hidden="true">
      <path fill="var(--berry)" d="M0 0 H480 V30 C470 45 455 60 440 55 C420 48 405 60 400 80 C395 95 380 95 378 80 C375 60 360 55 345 62 C320 72 300 60 290 80 C283 95 285 150 270 160 C255 168 240 158 240 140 C240 110 225 95 205 100 C185 106 180 95 175 80 C170 65 150 60 130 70 C110 80 100 95 90 120 C85 132 70 132 70 118 C70 95 60 70 45 70 C30 70 20 85 10 95 C5 100 0 98 0 92 Z"/>
    </svg>

    <div class="brand">
      <div><span class="brand__mark"></span><span class="brand__name">KELVO</span></div>
      <div class="brand__tagline">ACTIVE YOGHURT<br>DRINK</div>
    </div>

    <div class="product-title">
      <span class="product-title__word">Yogurt</span>
      <span class="product-title__type">DRINK</span>
    </div>

    <div class="fruit-visual" role="img" aria-label="Photo of three strawberries splashing into pink yoghurt"></div>

    <p class="flavour">Strawberry</p>

    <svg class="band band--bottom" viewBox="0 0 480 130" preserveAspectRatio="none" aria-hidden="true">
      <path fill="var(--berry)" d="M0 40 C60 20 110 30 170 50 C240 75 300 70 360 45 C410 25 450 20 480 0 V130 H0 Z"/>
    </svg>
    <p class="volume">300 ml</p>
  </main>
</body>
</html>
```